Lawn care business card

I am looking for a quality designed personal business card to represent the quality and elegant nature of our company. We separate ourselves in our market by the aesthetic value of our work, so I am looking for marketing material that does the same. We target our marketing high end customers, and we try to avoid price shoppers. I am open to all design options, so long as they are in line with our companies values.

We are tend to go with a retro look on everything from our logo and print material, to our uniforms. We like to portray and "old fashion" set of core values, with a modern elegance. So a wild and crazy look is out of the question.

Things I'd like on the card:
1.) Logo
2.) Phone number: (816) 555-2931
3.) Website: Verdelynkc.com
4.) Email: robertfairley@verdelynkc.com
5.) My name: Robert Fairley
6.) Facebook link: facebook.com/VerdelynGardenandGrounds
7.) Instagram: http://instagram.com/verdelynkc

Attached is a copy of our logo.

Reason: More time is needed to gather conclusive feedback from the members of our marketing team.

```html
<!DOCTYPE html>
<html lang="en">
<head>
<meta charset="utf-8">
<title>Verdelyn Business Card</title>
<link href="https://fonts.googleapis.com/css2?family=Arimo:wght@700&display=swap" rel="stylesheet">
<style>
  :root {
    --backdrop: #8d969e;
    --card: #1f2021;
    --ink: #f4f4f4;
    --accent: #e2622a;
  }
  html, body {
    margin: 0;
    padding: 0;
    width: 1200px;
    height: 1000px;
    overflow: hidden;
    background: var(--backdrop);
  }
  .canvas {
    position: relative;
    width: 1200px;
    height: 1000px;
  }
  .business-card {
    position: absolute;
    left: 100px;
    top: 214px;
    width: 1000px;
    height: 572px;
    background: var(--card);
    font-family: "Arimo", Arial, sans-serif;
    font-weight: 700;
    color: var(--ink);
    box-shadow: 0 6px 18px rgba(0, 0, 0, 0.25);
  }
  .brand {
    position: absolute;
    left: 70px;
    top: 300px;
    display: flex;
    align-items: center;
    gap: 16px;
  }
  .brand-dot {
    width: 54px;
    height: 54px;
    border-radius: 50%;
    background: var(--accent);
    flex: none;
  }
  .brand-name {
    font-size: 40px;
    letter-spacing: 1px;
    color: var(--ink);
  }
  .contact {
    position: absolute;
    left: 400px;
    top: 190px;
  }
  .contact-name {
    margin: 0 0 42px;
    font-size: 32px;
    font-weight: 700;
  }
  .contact-list {
    list-style: none;
    margin: 0;
    padding: 0;
    font-size: 20px;
    line-height: 38px;
    white-space: nowrap;
  }
</style>
</head>
<body>
  <main class="canvas">
    <section class="business-card">
      <div class="brand">
        <span class="brand-dot"></span>
        <span class="brand-name">Verdelyn</span>
      </div>
      <div class="contact">
        <h1 class="contact-name">Robert Fairley</h1>
        <ul class="contact-list">
          <li>Phone : (816) 555-2931</li>
          <li>Email : robertfairley@verdelynkc.com</li>
          <li>Website : Verdelynkc.com</li>
          <li>Instagram : http://instagram.com/verdelynkc</li>
          <li>Facebook : facebook.com/VerdelynGardenandGrounds</li>
        </ul>
      </div>
    </section>
  </main>
</body>
</html>
```